Business card design needed

We are a start up Mobile Vet Clinic.
We will be servicing an are that cover the Gladstone Region Shire.
Bookings will be made via the number listed or email address.
Travel will be charged

Target Market(s)

Pet Owners

Industry/Entity Type

Business

Contact Information for Business Card

TARRAWEN MOBILE VET
Durbanks Pty Ltd
Nora Whitcombe BVSc
27 Harrowgate St
Calliope QLD 4680

PH: 0749312864 Fax: 0749312906 email: tmvet@fernmail.com

Logo styles of interest
Pictorial/Combination Logo

```html
<!DOCTYPE html>
<html lang="en">
<head>
<meta charset="utf-8">
<title>Tarrawen Mobile Vet – Business Card</title>
<link href="https://fonts.googleapis.com/css2?family=Tinos:wght@400;700&display=swap" rel="stylesheet">
<style>
  :root {
    --teal: #5cbea6;
    --paper: #f6f6f6;
    --band: #e1f1ec;
    --ink: #111111;
    --edge-shadow: #0d2a22;
  }
  html, body {
    margin: 0;
    padding: 0;
    width: 1200px;
    height: 693px;
    overflow: hidden;
    background: var(--paper);
  }
  .card {
    position: relative;
    width: 1200px;
    height: 693px;
    overflow: hidden;
    font-family: "Tinos", "Times New Roman", serif;
    color: var(--ink);
  }
  .card__backdrop {
    position: absolute;
    inset: 0;
  }
  .card__line {
    position: absolute;
    margin: 0;
    font-size: 28px;
    line-height: 32px;
    white-space: nowrap;
    transform: translateX(-50%);
  }
  .card__business { left: 640px; top: 92px; font-size: 42px; line-height: 48px; font-weight: 700; letter-spacing: 1px; }
  .card__company  { left: 640px; top: 146px; font-size: 24px; }
  .card__title    { left: 620px; top: 236px; }
  .card__region   { left: 629px; top: 300px; }
  .card__cta      { left: 608px; top: 378px; }
  .card__vet      { left: 640px; top: 478px; font-size: 26px; }
  .card__address  { left: 640px; top: 516px; font-size: 24px; }
  .contact-band {
    position: absolute;
    left: 130px;
    right: 0;
    top: 609px;
    height: 39px;
    background: var(--band);
  }
  .contact-band__text {
    position: absolute;
    left: 34px;
    top: 1px;
    margin: 0;
    font-size: 34px;
    line-height: 37px;
    white-space: pre;
  }
</style>
</head>
<body>
  <div class="card">
    <svg class="card__backdrop" width="1200" height="693" viewBox="0 0 1200 693" aria-hidden="true">
      <defs>
        <filter id="edgeShadow" x="-20%" y="-5%" width="160%" height="110%">
          <feDropShadow dx="5" dy="0" stdDeviation="3" flood-color="#0d2a22" flood-opacity="0.95"/>
        </filter>
      </defs>
      <rect width="1200" height="693" fill="var(--teal)"/>
      <path d="M0 0 H152 C205 115 192 250 160 380 C135 480 118 600 180 693 H0 Z"
            fill="var(--paper)" filter="url(#edgeShadow)"/>
    </svg>

    <p class="card__line card__business">TARRAWEN MOBILE VET</p>
    <p class="card__line card__company">Durbanks Pty Ltd</p>

    <p class="card__line card__title">Mobile Vet Clinic</p>
    <p class="card__line card__region">Serving Gladstone Region Shire</p>
    <p class="card__line card__cta">Contact us today!</p>

    <p class="card__line card__vet">Nora Whitcombe BVSc</p>
    <p class="card__line card__address">27 Harrowgate St, Calliope QLD 4680</p>

    <div class="contact-band">
      <p class="contact-band__text">Phone: 0749312864   Fax: 0749312906   email:tmvet@fernmail.com</p>
    </div>
  </div>
</body>
</html>
```